Braek down, maintainance and support for satelite and TV

I want a website designed for a Dishwise firm i want it to look modern. I am finalizing the content with the underwriters at the moment so format we can start on the format and pictures. I want it to be easy to navigate with some eye capturing imiges. I am currently waiting for the underwriters to get the contact over so if we can start on everything else. I ONLY ADDED THE SCREEN SHOT AS I HAD TO ADD SOMETHING TO CONTINUE PLEASE USE YOUR OWN IDEAS

Target Market(s)

Every one

Industry/Entity Type

Tv

Number of Pages Required

5+ page

Font styles to use
Sans Serif

```html
<!DOCTYPE html>
<html lang="en">
<head>
<meta charset="utf-8">
<title>Dishwise</title>
<link rel="stylesheet" href="https://fonts.googleapis.com/css2?family=Roboto+Condensed:wght@300;400;700&family=Open+Sans:ital,wght@0,400;0,600;0,700;1,400&display=swap">
<style>
:root{
  --dark:#3b3b3b;
  --teal:#1a9ea8;
  --teal-deep:#0d9bb0;
  --orange:#ef9a12;
  --orange-deep:#e8760f;
  --red:#d92027;
  --steel:#5f8fba;
  --paper:#ece9e4;
  --card:#f4f4f4;
  --ink:#333333;
  --white:#ffffff;
  --field:#ececec;
}
*{margin:0;padding:0;box-sizing:border-box}
html,body{width:1200px;height:2965px;overflow:hidden}
body{position:relative;background:var(--paper);font-family:"Open Sans",Arial,sans-serif;color:var(--ink)}
.abs{position:absolute}

/* header */
.topbar{left:0;top:0;width:1200px;height:110px;background:var(--dark)}
.brand{left:84px;top:34px;display:flex;align-items:center;gap:12px;color:var(--white);font-family:"Open Sans",sans-serif;font-weight:400;font-size:30px;line-height:40px}
.brand-dot{width:26px;height:26px;border-radius:50%;background:var(--teal)}
.social-top{right:150px;top:12px;display:flex;gap:6px}
.dot{width:30px;height:30px;border-radius:50%;border:2px solid #888}
.navbar{left:0;top:110px;width:1200px;height:56px;background:linear-gradient(#fafafa,#dcdcdc);border-bottom:1px solid #c8c8c8}
.nav{left:75px;top:110px;display:flex;height:56px}
.nav a{display:block;padding:0 17px;line-height:56px;border-left:1px solid #c6c6c6;font-family:"Roboto Condensed",sans-serif;font-size:17px;color:#444;text-decoration:none}
.nav a:last-child{border-right:1px solid #c6c6c6}
.help-tab{left:858px;top:60px;width:246px;height:42px;background:var(--teal);color:var(--white);border-radius:6px 6px 0 0;text-align:center;line-height:42px;font-family:"Roboto Condensed",sans-serif;font-size:17px}
.help-phone{left:840px;top:100px;width:282px;height:68px;background:var(--orange);color:var(--white);text-align:center;line-height:68px;font-family:"Roboto Condensed",sans-serif;font-size:33px;clip-path:polygon(4% 0,96% 0,100% 50%,96% 100%,4% 100%,0 50%)}
.help-mail{left:855px;top:163px;width:250px;height:30px;background:var(--white);border-radius:4px;box-shadow:0 2px 4px rgba(0,0,0,.3);text-align:center;line-height:30px;font-size:15px;color:#222}

/* hero */
.hero{left:0;top:166px;width:1200px;height:578px;background:linear-gradient(180deg,#3e5579 0%,#5c5f7c 45%,#8a6a72 70%,#2c2a3a 100%)}
.hero-title{left:100px;top:388px;color:var(--white);font-family:"Roboto Condensed",sans-serif;line-height:40px;text-shadow:0 2px 4px rgba(0,0,0,.5)}
.hero-title strong{display:block;font-size:40px;font-weight:700}
.hero-title span{display:block;font-size:33px;font-weight:300}
.live-chat{left:0;top:360px;width:48px;height:160px;background:var(--red);border-radius:0 8px 8px 0;border:2px solid #fff;border-left:none}
.live-chat span{position:absolute;left:50%;top:50%;transform:translate(-50%,-50%) rotate(-90deg);color:#fff;font-family:"Roboto Condensed",sans-serif;font-size:19px;white-space:nowrap}
.consult{left:795px;top:228px;width:330px;height:447px;background:var(--white);border-radius:6px;box-shadow:0 3px 10px rgba(0,0,0,.4);overflow:hidden}
.consult-head{height:122px;background:var(--teal);color:var(--white);text-align:center;padding-top:12px;clip-path:polygon(0 0,100% 0,100% 85%,50% 100%,0 85%)}
.consult-head .k{font-family:"Roboto Condensed",sans-serif;font-size:16px}
.consult-head .big{display:inline-block;margin:6px 0;padding:0 22px;background:#1f3d48;border-radius:20px;font-family:"Roboto Condensed",sans-serif;font-size:28px;line-height:36px}
.consult-head .s{font-size:12px;line-height:17px;padding:0 40px}
.field{margin:13px 17px 0;height:38px;background:var(--field);border-radius:4px;padding:0 12px;line-height:38px;font-size:12px;color:#555}
.field.area{height:76px;line-height:22px;padding-top:8px}
.submit{margin:14px 17px 0;height:40px;background:var(--orange);border-radius:4px;color:#fff;text-align:center;line-height:40px;font-family:"Roboto Condensed",sans-serif;font-weight:700;font-size:17px;letter-spacing:1px}

/* services */
.band{left:0;top:1060px}
.service{top:810px;width:330px;height:430px;background:var(--card);border-radius:8px;box-shadow:0 2px 8px rgba(0,0,0,.18);text-align:center;overflow:hidden}
.service .glow{position:absolute;left:0;top:0;width:330px;height:150px;background:radial-gradient(ellipse at 60% 0,#f4e3cc 0,#f4e3cc 55%,transparent 56%)}
.service .icon{position:absolute;left:105px;top:-2px;width:120px;height:120px;border-radius:50%;background:var(--teal);border:6px solid #e6e6e6}
.service .icon svg{position:absolute;left:28px;top:28px}
.service h3{position:absolute;top:132px;width:100%;font-family:"Roboto Condensed",sans-serif;font-weight:400;font-size:26px;color:#222}
.service p{position:absolute;top:184px;left:30px;right:30px;font-size:12.5px;line-height:24px;color:#555}
.btn-ghost{display:inline-block;border:1.5px solid #8bb0cf;border-radius:6px;color:#6a95c0;font-size:12px;padding:0 22px;line-height:38px}
.service .btn-ghost{position:absolute;left:100px;top:355px;width:130px;padding:0}

.testi-title{left:88px;top:1305px;color:var(--white);font-family:"Roboto Condensed",sans-serif;font-weight:300;font-size:44px;display:flex;align-items:center;gap:18px}
.quote{left:240px;top:1472px;width:720px;text-align:center;font-style:italic;font-size:15.5px;line-height:25px;color:#555}
.quote-name{left:0;top:1562px;width:1200px;text-align:center;font-weight:600;font-size:15px;color:#222;letter-spacing:.5px}
.qmark{top:1480px;color:var(--teal);font-family:Georgia,serif;font-size:60px;line-height:40px}

/* welcome */
.teal-band{left:0;top:1668px;width:1200px;height:578px;background:var(--teal-deep)}
.welcome{left:75px;top:1647px;width:783px;height:560px;background:var(--white);border-top:5px solid var(--teal-deep);box-shadow:0 4px 10px rgba(0,0,0,.3)}
.portrait{left:22px;top:25px;width:222px;height:508px;background:linear-gradient(160deg,#e9e6df,#b9b2a8 50%,#6c6760)}
.welcome-body{left:270px;top:18px;width:490px}
.welcome-body .k{font-family:"Roboto Condensed",sans-serif;font-size:21px;color:#333;line-height:22px}
.welcome-body h2{font-family:"Roboto Condensed",sans-serif;font-weight:300;font-size:30px;color:#3d8fb8;line-height:34px}
.welcome-body p{font-size:13.8px;line-height:24px;color:#444;margin-top:12px}
.welcome .btn-ghost{position:absolute;left:270px;top:497px;width:134px;padding:0;text-align:center}
.news-head{left:858px;top:1688px;width:342px;height:58px;background:var(--orange);color:#fff;font-family:"Roboto Condensed",sans-serif;font-size:23px;line-height:58px;padding-left:26px}
.news{left:884px;width:290px;color:#fff}
.news .d{font-size:11px;opacity:.85}
.news h4{font-size:13.5px;line-height:20px;font-weight:700;margin-top:2px}
.news p{font-size:13.5px;line-height:21px;margin-top:8px}
.news .more{font-size:11.5px;font-weight:700;margin-top:8px}

/* map */
.map{left:0;top:2246px;width:1200px;height:230px;background:linear-gradient(180deg,#ddd9cf,#e8e4da)}
.pin{left:593px;top:2280px}

/* footer */
.footer{left:0;top:2476px;width:1200px;height:489px;background:var(--dark)}
.foot-photo{left:0;top:2476px}
.f-h{font-family:"Roboto Condensed",sans-serif;font-size:19px;color:#fff}
.f-rule{height:1px;background:#5a5a5a}
.f-info{top:2572px;display:flex;gap:14px;color:#ddd;font-size:13px;line-height:24px}
.f-ico{width:30px;height:30px;border-radius:50%;border:2px solid #ddd;flex:none;margin-top:4px;position:relative}
.links{left:72px;top:2730px;color:#ddd;font-size:13px;line-height:27.5px;list-style:none}
.f-field{left:360px;width:244px;height:38px;background:var(--field);border-radius:4px;font-size:12.5px;line-height:38px;padding-left:14px;color:#555}
.f-sub{left:360px;top:2832px;width:244px;height:38px;background:var(--orange-deep);border-radius:4px;color:#fff;text-align:center;line-height:38px;font-weight:700;font-size:14px}
.f-social{left:650px;top:2732px;display:flex;gap:6px}
.f-social .dot{border-color:#ddd;width:33px;height:33px}
.foot-brand{left:1010px;top:2864px;display:flex;align-items:center;gap:10px;color:var(--ink);font-family:"Open Sans",sans-serif;font-weight:400;font-size:26px;line-height:34px}
.foot-brand .brand-dot{width:20px;height:20px}
.copy{left:0;top:2925px;width:1200px;height:40px;padding-left:74px;line-height:40px;color:#eee;font-size:13.5px}
</style>
</head>
<body>

<!-- header -->
<div class="abs topbar"></div>
<div class="abs brand"><span class="brand-dot"></span>Dishwise</div>
<div class="abs social-top"><span class="dot"></span><span class="dot"></span><span class="dot"></span><span class="dot"></span></div>
<div class="abs navbar"></div>
<nav class="abs nav"><a>HOME</a><a>ABOUT US</a><a>SERVICES</a><a>NEWS</a><a>CONTACT US</a></nav>

<!-- hero -->
<div class="abs hero" role="img" aria-label="Photo of a satellite dish silhouetted against a city skyline at dusk"></div>
<div class="abs help-tab">NEED HELP? CONTACT US!</div>
<div class="abs help-phone">1-000-000-0000</div>
<div class="abs help-mail">info@dishwise.com</div>
<div class="abs hero-title"><strong>Lorem ipsum dolor sit amet,</strong><span>consectetur adipiscing elit</span></div>
<div class="abs live-chat"><span>LIVE CHAT</span></div>
<form class="abs consult">
  <div class="consult-head">
    <div class="k">CONTACT US TODAY FOR YOUR</div>
    <div class="big">FREE CONSULTATION</div>
    <div class="s">Fill out the form below and we'll be in touch within 24 hours!</div>
  </div>
  <div class="field">Name</div>
  <div class="field">Email</div>
  <div class="field">Phone</div>
  <div class="field area">How Can we help you?</div>
  <div class="submit">SUBMIT</div>
</form>

<!-- services + testimonial band -->
<svg class="abs band" width="1200" height="380" viewBox="0 0 1200 380">
  <polygon fill="var(--steel)" points="0,125 1200,10 1200,305 310,348 298,378 282,352 0,362"/>
</svg>

<div class="abs service" style="left:75px">
  <div class="glow"></div>
  <div class="icon"><svg width="52" height="52" viewBox="0 0 52 52" fill="none" stroke="#fff" stroke-width="3"><rect x="12" y="12" width="28" height="28" rx="3"/><rect x="20" y="20" width="12" height="12"/><path d="M18 4v8M26 4v8M34 4v8M18 40v8M26 40v8M34 40v8M4 18h8M4 26h8M4 34h8M40 18h8M40 26h8M40 34h8"/></svg></div>
  <h3>SWITCH TO DIGITAL</h3>
  <p>Lorem ipsum dolor sit amet, consectetur adipiscing elit, sed do eiusmod tempor incididunt ut labore et dolore magna aliqua. Ut enim ad minim veniam, quis nostrud exercitation ullamco laboris nisi ut aliquip ex ea commodo consequat.</p>
  <span class="btn-ghost">READ MORE</span>
</div>
<div class="abs service" style="left:435px">
  <div class="glow"></div>
  <div class="icon"><svg width="52" height="52" viewBox="0 0 52 52" fill="none" stroke="#fff" stroke-width="3"><circle cx="16" cy="34" r="8"/><circle cx="16" cy="34" r="3"/><circle cx="32" cy="42" r="5"/><path d="M28 26l16-16 4 4-16 16z"/></svg></div>
  <h3>SERVICE AND REPAIRS</h3>
  <p>Lorem ipsum dolor sit amet, consectetur adipiscing elit, sed do eiusmod tempor incididunt ut labore et dolore magna aliqua. Ut enim ad minim veniam, quis nostrud exercitation ullamco laboris nisi ut aliquip ex ea commodo consequat.</p>
  <span class="btn-ghost">READ MORE</span>
</div>
<div class="abs service" style="left:795px">
  <div class="glow"></div>
  <div class="icon"><svg width="52" height="52" viewBox="0 0 52 52" fill="none" stroke="#fff" stroke-width="3"><path d="M26 6a20 20 0 1 1-18 11"/><path d="M26 14v12l8 6"/><path d="M4 12l4 6 6-3"/></svg></div>
  <h3>SAME DAY SERVICE</h3>
  <p>Lorem ipsum dolor sit amet, consectetur adipiscing elit, sed do eiusmod tempor incididunt ut labore et dolore magna aliqua. Ut enim ad minim veniam, quis nostrud exercitation ullamco laboris nisi ut aliquip ex ea commodo consequat.</p>
  <span class="btn-ghost">READ MORE</span>
</div>

<div class="abs testi-title"><span style="font-family:Georgia,serif;font-size:64px;line-height:40px;padding-top:22px">&#8220;</span>CLIENT TESTIMONIAL</div>
<div class="abs qmark" style="left:180px">&#8220;</div>
<div class="abs qmark" style="left:975px">&#8221;</div>
<p class="abs quote">Sed ut perspiciatis unde omnis iste natus error sit voluptatem accusantium doloremque laudantium, totam rem aperiam, eaque ipsa quae ab illo inventore veritatis et quasi architecto beatae vitae dicta sunt explicabo.</p>
<div class="abs quote-name">MARCUS HALE</div>

<!-- welcome + news -->
<div class="abs teal-band"></div>
<section class="abs welcome">
  <div class="abs portrait" role="img" aria-label="Portrait photo of a smiling engineer holding a tablet"></div>
  <div class="abs welcome-body">
    <div class="k">WELCOME TO</div>
    <h2>DISHWISE</h2>
    <p>Lorem ipsum dolor sit amet, consectetur adipiscing elit, sed do eiusmod tempor incididunt ut labore et dolore magna aliqua. Ut enim ad minim veniam, quis nostrud exercitation ullamco laboris nisi ut aliquip ex ea commodo consequat. Duis aute irure dolor in reprehenderit in voluptate velit esse cillum dolore eu fugiat nulla pariatur. Excepteur sint occaecat cupidatat non proident, sunt in culpa qui officia deserunt mollit anim id est laborum.</p>
    <p>be taken in order to make an effective personal injury claim. I know how adjusters think and what they are trained to do when handling injury claims. With me on your side, you can be sure that you won't be short-changed and that you will get what you deserve for your injuries. With me on your side, you can be sure that you won't be short-changed and that you will get what you deserve for your injuries. With me on your side, you can be sure that you won't be short-changed.</p>
  </div>
  <span class="btn-ghost">READ MORE</span>
</section>
<div class="abs news-head">LATEST NEWS</div>
<article class="abs news" style="top:1768px">
  <div class="d">16 JAN 2016</div>
  <h4>Lorem ipsum dolor sit amet, consectetur adipiscing elit</h4>
  <p>Lorem ipsum dolor sit amet, consectetur adipiscing elit, sed do eiusmod tempor.</p>
  <div class="more">READ MORE</div>
</article>
<article class="abs news" style="top:1954px">
  <div class="d">16 JAN 2016</div>
  <h4>Lorem ipsum dolor sit amet, consectetur adipiscing elit</h4>
  <p>Lorem ipsum dolor sit amet, consectetur adipiscing elit, sed do eiusmod tempor.</p>
  <div class="more">READ MORE</div>
</article>

<!-- map -->
<div class="abs map" role="img" aria-label="Street map showing the office location"></div>
<svg class="abs pin" width="70" height="90" viewBox="0 0 70 90">
  <path d="M35 88L14 56A32 32 0 1 1 56 56Z" fill="#333"/>
  <circle cx="35" cy="32" r="24" fill="var(--teal)"/>
</svg>

<!-- footer -->
<div class="abs footer"></div>
<svg class="abs foot-photo" width="1200" height="489" viewBox="0 0 1200 489">
  <defs><linearGradient id="ph" x1="0" y1="0" x2="1" y2="1"><stop offset="0" stop-color="#5a5a5a"/><stop offset=".6" stop-color="#c9b9a6"/><stop offset="1" stop-color="#efe6dc"/></linearGradient></defs>
  <polygon points="880,0 1200,0 1200,175 1048,215" fill="url(#ph)" role="img" aria-label="Photo of a smiling support agent wearing a headset"/>
  <polygon points="1200,165 1200,489 820,489" fill="#fff"/>
</svg>

<div class="abs f-h" style="left:75px;top:2510px">OUR OFFICE LOCATION</div>
<div class="abs f-rule" style="left:72px;top:2550px;width:242px"></div>
<div class="abs f-rule" style="left:72px;top:2633px;width:242px"></div>
<div class="abs f-rule" style="left:360px;top:2550px;width:242px"></div>
<div class="abs f-rule" style="left:360px;top:2633px;width:242px"></div>
<div class="abs f-rule" style="left:650px;top:2550px;width:242px"></div>
<div class="abs f-rule" style="left:650px;top:2633px;width:242px"></div>
<div class="abs f-info" style="left:72px"><span class="f-ico"><svg width="26" height="26" viewBox="0 0 26 26"><path d="M13 21l-5-8a6 6 0 1 1 10 0z" fill="#ddd"/><circle cx="13" cy="10" r="2" fill="#3b3b3b"/></svg></span><span>228, Lorem Ipsum dolor sit,<br>Dosis amet sit - 85485</span></div>
<div class="abs f-info" style="left:360px"><span class="f-ico"><svg width="26" height="26" viewBox="0 0 26 26"><path d="M8 6l3 0 1 4-2 1.5a9 9 0 0 0 4.5 4.5L16 14l4 1v3c-7 1-13-5-12-12z" fill="#ddd"/></svg></span><span>Phone:<br>1-000-000-0000</span></div>
<div class="abs f-info" style="left:650px"><span class="f-ico"><svg width="26" height="26" viewBox="0 0 26 26"><rect x="6" y="8" width="14" height="10" fill="none" stroke="#ddd" stroke-width="1.6"/><path d="M6 8l7 6 7-6" fill="none" stroke="#ddd" stroke-width="1.6"/></svg></span><span>Email<br>info@dishwise.com</span></div>

<div class="abs f-h" style="left:72px;top:2688px">QUICK LINKS</div>
<ul class="abs links"><li>Home</li><li>About Us</li><li>Services</li><li>News</li><li>Contact Us</li></ul>
<div class="abs f-h" style="left:360px;top:2688px">SUBSCRIBE NEWSLETTER</div>
<div class="abs f-field" style="top:2735px">Name</div>
<div class="abs f-field" style="top:2784px">Email</div>
<div class="abs f-sub">SUBSCRIBE</div>
<div class="abs f-h" style="left:650px;top:2688px">CONNECT WITH US</div>
<div class="abs f-social"><span class="dot"></span><span class="dot"></span><span class="dot"></span><span class="dot"></span></div>
<div class="abs foot-brand"><span class="brand-dot"></span>Dishwise</div>
<div class="abs copy">©2016 Dishwise. All Rights Reserved. All rights reserved &nbsp;| &nbsp;Disclaimer &nbsp;| &nbsp;Site Map &nbsp;| &nbsp;Privacy Policy</div>

</body>
</html>
```